Web design

We need the design for the logo and website for a women fashion website. No coding required. The colors used should be neutral (maybe with a light touch of color), the style should be modern, slightly luxurious, not too crowded. The target market is young professionals who love trendy clothes.
Updates

Need extra days to review

Target Market(s)

Young professionals

Industry/Entity Type

Apparel

Number of Pages Required

5+ page

Font styles to use
Sans Serif
Other font styles liked:
• Montserrat, Engravers Gothic, Benton Sans, gotham-book

Colors

Designer to choose colors to be used in the design.

```html
<!DOCTYPE html>
<html lang="en">
<head>
<meta charset="utf-8">
<title>SERAH — Women's Fashion</title>
<link href="https://fonts.googleapis.com/css2?family=Montserrat:wght@400;500;600;700;800&display=swap" rel="stylesheet">
<style>
:root{
  --ink:#24232f;
  --muted:#6f6d76;
  --peach:#f1d6c5;
  --sand:#dcc7ae;
  --line:#e6e3df;
  --soft:#fafafa;
  --night:#2e2b48;
  --night-text:#b9b6cf;
}
*{box-sizing:border-box;margin:0;padding:0}
html,body{width:1200px;height:3530px;overflow:hidden}
body{position:relative;font-family:"Montserrat",sans-serif;color:var(--ink);background:#fff}
.abs{position:absolute}
.photo{position:absolute;display:block}

/* header */
.logo{position:absolute;font-weight:700;letter-spacing:3px;font-size:25px;line-height:30px}
.nav{position:absolute;top:44px;left:301px;display:flex;gap:40px;font-size:13px}
.nav span{display:flex;align-items:center;gap:6px}
.search{position:absolute;left:639px;top:31px;width:220px;height:40px;background:#fff;border:1px solid var(--line);font-size:12px;color:#c9c6c2;padding:13px 14px}
.search svg{position:absolute;right:10px;top:11px}
.icon{position:absolute;top:38px}
.badge{position:absolute;top:-6px;right:-8px;width:14px;height:14px;border-radius:50%;background:#fff;border:1px solid var(--ink);font-size:9px;text-align:center;line-height:12px}

/* hero */
.hero{position:absolute;left:0;top:0;width:1200px;height:625px;background:var(--peach)}
.hero-photo{left:610px;top:60px;width:590px;height:565px;background:linear-gradient(160deg,#e9c9b2,#d8b197 55%,#a9bccd)}
.kicker{position:absolute;left:154px;top:217px;font-size:13px;letter-spacing:2px;color:#5b5350}
.hero h1{position:absolute;left:154px;top:250px;font-size:45px;line-height:54px;font-weight:800;letter-spacing:.5px}
.hero p{position:absolute;left:156px;top:378px;font-size:12.5px;line-height:24px;color:#4b4544}
.btn{position:absolute;display:flex;align-items:center;justify-content:center;gap:10px;border-radius:30px;font-weight:700;font-size:14px;color:var(--ink)}
.btn-white{background:#fff}
.btn-sand{background:var(--sand)}
.dots{position:absolute;display:flex;gap:20px;align-items:center}
.dots i{display:block;width:8px;height:8px;border-radius:50%;background:#cdb7a4}
.dots i.on{background:var(--ink)}

/* features */
.features{position:absolute;top:625px;left:0;width:1200px;height:89px;background:var(--soft);border-bottom:1px solid var(--line)}
.feature{position:absolute;top:0;height:89px;display:flex;align-items:center;gap:22px}
.feature h4{font-weight:500;font-size:14px;margin-bottom:6px}
.feature small{font-size:11.5px;color:var(--muted)}
.divider{position:absolute;top:0;width:1px;height:89px;background:var(--line)}

/* promo */
.promo-left{left:154px;top:759px;width:509px;height:314px;background:linear-gradient(100deg,#f2ede7 0%,#ead9c6 50%,#c99b7c 100%)}
.promo-right{left:689px;top:759px;width:355px;height:314px;background:linear-gradient(110deg,#e8e4e2,#b9a8a0 50%,#b33a35 80%,#7d6152)}
.promo-title{position:absolute;font-weight:600}

/* sections */
.section-title{position:absolute;left:0;width:1200px;text-align:center;font-weight:600;font-size:24px}
.card-img{position:absolute;width:205px;height:262px}
.cart{position:absolute;bottom:0;left:0;width:100%;height:28px;background:#2f2f36;color:#fff;font-size:10.5px;font-weight:600;text-align:center;line-height:28px}
.card-name{position:absolute;font-size:13.5px;color:var(--muted)}
.card-price{position:absolute;font-size:14px}

/* banner */
.banner{left:0;top:1560px;width:1200px;height:411px;background:linear-gradient(90deg,#b9a58e 0%,#a5836c 30%,#d4c8bb 55%,#f3f1ee 75%,#fbfbfa 100%)}
.banner-strip{position:absolute;left:690px;top:1806px;width:510px;height:80px;background:rgba(235,235,235,.55)}

/* feed */
.gram-tile{position:absolute;top:2973px;width:198px;height:212px}

/* footer */
.footer{position:absolute;left:0;top:3190px;width:1200px;height:340px;background:var(--night);color:var(--night-text)}
.footer h5{position:absolute;font-weight:500;font-size:15px;color:#dedcec}
.footer a{position:absolute;font-size:12.5px;color:var(--night-text);text-decoration:none}
.footer .note{position:absolute;font-size:11px;line-height:24px}
.news-input{position:absolute;left:741px;top:158px;width:303px;height:42px;border:1px solid #5d5a7a;font-size:11px;color:#6d6a8a;padding:14px 16px}
.news-input b{position:absolute;right:0;top:0;width:128px;height:40px;border-left:1px solid #5d5a7a;color:#fff;font-size:12px;letter-spacing:2px;text-align:center;line-height:40px}
.social{position:absolute;width:17px;height:17px;border:1.5px solid var(--night-text);border-radius:4px}
</style>
</head>
<body>

<!-- hero -->
<section class="hero">
  <div class="photo hero-photo" role="img" aria-label="Young woman with long wavy hair and sunglasses in a light knit top"></div>
  <div class="kicker">New Arrival</div>
  <h1>Get Latest<br>Trends On Reveal</h1>
  <p>Does it get any more summertime than a classic summer dress?<br>This wardrobe icon has earned its rightful place on our list of sunshine.</p>
  <div class="btn btn-white" style="left:154px;top:448px;width:152px;height:45px">Shop Now
    <svg width="20" height="10" viewBox="0 0 20 10"><path d="M0 5h18M14 1l4 4-4 4" fill="none" stroke="#24232f" stroke-width="1.6"/></svg></div>
  <div class="dots" style="left:167px;top:531px"><i></i><i class="on"></i><i></i></div>
</section>

<!-- header -->
<header>
  <div class="logo" style="left:158px;top:42px">SERAH</div>
  <nav class="nav"><span>Latest Arivals</span><span>Clothes
    <svg width="9" height="6" viewBox="0 0 9 6"><path d="M1 1l3.5 3.5L8 1" fill="none" stroke="#24232f" stroke-width="1.3"/></svg></span><span>On Sale</span></nav>
  <div class="search">Search
    <svg width="16" height="16" viewBox="0 0 16 16"><circle cx="7" cy="7" r="5" fill="none" stroke="#bdb9b5" stroke-width="1.4"/><path d="M11 11l4 4" stroke="#bdb9b5" stroke-width="1.4"/></svg></div>
  <svg class="icon" style="left:876px" width="20" height="24" viewBox="0 0 20 24"><circle cx="10" cy="7" r="5" fill="none" stroke="#6a5d55" stroke-width="1.4"/><path d="M1 23c0-5 4-8 9-8s9 3 9 8" fill="none" stroke="#6a5d55" stroke-width="1.4"/></svg>
  <div class="icon" style="left:914px;width:24px;height:22px">
    <svg width="24" height="22" viewBox="0 0 24 22"><path d="M12 20S2 14 2 7a5 5 0 0110-1 5 5 0 0110 1c0 7-10 13-10 13z" fill="none" stroke="#6a5d55" stroke-width="1.4"/></svg><span class="badge">1</span></div>
  <div class="icon" style="left:966px;width:22px;height:24px">
    <svg width="22" height="24" viewBox="0 0 22 24"><rect x="2" y="7" width="18" height="16" fill="none" stroke="#6a5d55" stroke-width="1.4"/><path d="M7 7a4 4 0 018 0" fill="none" stroke="#6a5d55" stroke-width="1.4"/></svg><span class="badge">1</span></div>
  <svg class="icon" style="left:1010px" width="34" height="22" viewBox="0 0 34 22"><circle cx="11" cy="11" r="10" fill="#2d3b7a"/><path d="M26 9l3 3 3-3" fill="none" stroke="#24232f" stroke-width="1.3"/></svg>
</header>

<!-- features -->
<section class="features">
  <div class="feature" style="left:183px">
    <svg width="46" height="46" viewBox="0 0 46 46"><circle cx="22" cy="24" r="18" fill="none" stroke="#d6b89a" stroke-width="1.6"/><path d="M4 24h36M22 6c-8 10-8 26 0 36M22 6c8 10 8 26 0 36" fill="none" stroke="#d6b89a" stroke-width="1.4"/></svg>
    <div><h4>Shipping Worldwide</h4><small>Fast Free Shipping</small></div></div>
  <div class="divider" style="left:446px"></div>
  <div class="feature" style="left:502px">
    <svg width="46" height="40" viewBox="0 0 46 40"><rect x="2" y="8" width="26" height="20" fill="none" stroke="#d6b89a" stroke-width="1.6"/><path d="M28 14h9l7 8v6H28z" fill="none" stroke="#d6b89a" stroke-width="1.6"/><circle cx="11" cy="31" r="4" fill="#fff" stroke="#d6b89a" stroke-width="1.6"/><circle cx="36" cy="31" r="4" fill="#fff" stroke="#d6b89a" stroke-width="1.6"/></svg>
    <div><h4>Free Us Delivery</h4><small>On orders over $200!</small></div></div>
  <div class="divider" style="left:751px"></div>
  <div class="feature" style="left:782px">
    <svg width="48" height="46" viewBox="0 0 48 46"><path d="M10 14l18-10 18 10v20L28 44 10 34z" fill="none" stroke="#d6b89a" stroke-width="1.6"/><path d="M10 14l18 10 18-10M28 24v20" fill="none" stroke="#d6b89a" stroke-width="1.6"/><path d="M4 30a8 8 0 0010 8" fill="none" stroke="#d6b89a" stroke-width="1.6"/></svg>
    <div><h4>30 Days Return</h4><small>within 30 days for an exchange</small></div></div>
</section>

<!-- promo tiles -->
<div class="photo promo-left" role="img" aria-label="Woman in a sun hat and white polka dot dress by a ship at sunset"></div>
<div class="promo-title" style="left:207px;top:818px;font-size:19px">The Hotlist of</div>
<div class="promo-title" style="left:207px;top:845px;font-size:36px;font-weight:700;letter-spacing:1px">SUMMER</div>
<div class="abs" style="left:182px;top:903px;width:5px;height:5px;border-radius:50%;background:var(--ink)"></div>
<div class="abs" style="left:182px;top:925px;width:5px;height:5px;border-radius:50%;background:#cfc9c2"></div>
<div class="abs" style="left:211px;top:900px;font-size:12px;line-height:24px">The 12 Biggest Spring &amp;<br>Summer 2021 Trends</div>
<div class="btn btn-sand" style="left:209px;top:961px;width:108px;height:31px;font-size:10px">Shop Now
  <svg width="16" height="8" viewBox="0 0 16 8"><path d="M0 4h14M11 1l3 3-3 3" fill="none" stroke="#24232f" stroke-width="1.4"/></svg></div>

<div class="photo promo-right" role="img" aria-label="Woman in a red lace gown seated on an ornate chair"></div>
<div class="promo-title" style="left:713px;top:870px;font-size:28px;font-weight:700">Street Style</div>
<div class="promo-title" style="left:713px;top:910px;font-size:16px">Has it Own Rules</div>
<div class="btn" style="left:713px;top:954px;width:82px;height:25px;font-size:9px;background:rgba(255,255,255,.7)">Shop Now
  <svg width="12" height="8" viewBox="0 0 12 8"><path d="M0 4h10M7 1l3 3-3 3" fill="none" stroke="#24232f" stroke-width="1.3"/></svg></div>
<div class="abs" style="left:731px;top:1002px;display:flex;gap:10px">
  <i style="width:6px;height:6px;border-radius:50%;background:var(--ink)"></i>
  <i style="width:6px;height:6px;border-radius:50%;border:1px solid var(--ink)"></i>
  <i style="width:6px;height:6px;border-radius:50%;border:1px solid var(--ink)"></i></div>

<!-- latest collection -->
<h2 class="section-title" style="top:1116px">Latest Collection</h2>
<div class="card-img" style="left:155px;top:1196px;background:linear-gradient(180deg,#e7ece8,#d8cfa3)" role="img" aria-label="Woman in a yellow floral slip dress"><div class="cart">ADD TO CART</div></div>
<div class="card-img" style="left:383px;top:1196px;background:linear-gradient(180deg,#bfc1b5,#9b5b3c 60%,#6f7a5a)" role="img" aria-label="Woman in a rust jumpsuit with a dark coat among plants"></div>
<div class="card-img" style="left:613px;top:1196px;background:linear-gradient(180deg,#c8cdd2,#37528e 50%,#d6c26f)" role="img" aria-label="Woman in a navy jacket and floral skirt on a city street"></div>
<div class="card-img" style="left:839px;top:1196px;background:linear-gradient(180deg,#9fa18e,#d99c3b 60%,#c7a17b)" role="img" aria-label="Woman in an orange dress reading in a chair"></div>
<div class="card-name" style="left:157px;top:1473px">Textured vegan leather</div><div class="card-price" style="left:157px;top:1499px">$ 69.00</div>
<div class="card-name" style="left:384px;top:1473px">Textured vegan leather</div><div class="card-price" style="left:384px;top:1499px">$ 69.00</div>
<div class="card-name" style="left:614px;top:1473px">Textured vegan leather</div><div class="card-price" style="left:614px;top:1499px">$ 69.00</div>
<div class="card-name" style="left:840px;top:1473px">Textured vegan leather</div><div class="card-price" style="left:840px;top:1499px">$ 69.00</div>

<!-- banner -->
<div class="photo banner" role="img" aria-label="Woman in a dusty pink dress seated in a bright boutique"></div>
<div class="banner-strip"></div>
<div class="abs" style="left:688px;top:1656px;font-size:24px;font-weight:500">FIND YOUR</div>
<div class="abs" style="left:688px;top:1693px;font-size:38px;font-weight:600;letter-spacing:1px">PERFECT FASHION</div>
<div class="abs" style="left:692px;top:1752px;font-size:12.5px;line-height:24px;color:#4b4544">Contemporary wardrobe staples and authentic style<br>for the modern man and women.</div>
<div class="btn btn-sand" style="left:685px;top:1824px;width:150px;height:45px">Shop Now
  <svg width="20" height="10" viewBox="0 0 20 10"><path d="M0 5h18M14 1l4 4-4 4" fill="none" stroke="#24232f" stroke-width="1.6"/></svg></div>

<!-- trending -->
<h2 class="section-title" style="top:2014px;left:20px">Trending Looks Near You</h2>
<div class="card-img" style="left:27px;top:2084px;background:linear-gradient(180deg,#f4f4f2,#e8d48a 60%,#f1ede6)" role="img" aria-label="Model in a yellow and cream dress"><div class="cart">ADD TO CART</div></div>
<div class="card-img" style="left:270px;top:2084px;background:linear-gradient(180deg,#f1f1ef,#7e8f68 50%,#eeeeec)" role="img" aria-label="Model in a sage green button dress"></div>
<div class="card-img" style="left:508px;top:2084px;background:linear-gradient(180deg,#f1f1ef,#e2cbbb 50%,#b88a6e)" role="img" aria-label="Model in a polka dot off-shoulder top"></div>
<div class="card-img" style="left:748px;top:2084px;background:linear-gradient(180deg,#f1f1ef,#ecd9cf 50%,#c9695a)" role="img" aria-label="Model in a blush blouse and red trousers"></div>
<div class="card-img" style="left:978px;top:2084px;background:linear-gradient(180deg,#f1f1ef,#7f8faf 50%,#eeeeec)" role="img" aria-label="Model in a chambray shirt dress"></div>
<div class="card-img" style="left:27px;top:2437px;background:linear-gradient(180deg,#f3f3f3,#8fb4dd 55%,#e9eef4)" role="img" aria-label="Model in a blue tie-dye maxi dress"></div>
<div class="card-img" style="left:270px;top:2437px;background:linear-gradient(180deg,#f3f3f3,#e9dfd6 40%,#6d9a6e 70%,#d46d58)" role="img" aria-label="Model in a tropical print wrap dress"></div>
<div class="card-img" style="left:508px;top:2437px;background:linear-gradient(180deg,#f3f3f3,#f4e16a 55%,#f1efe6)" role="img" aria-label="Model in a yellow halter dress"></div>
<div class="card-img" style="left:748px;top:2437px;background:linear-gradient(180deg,#f3f3f3,#232226 50%,#ececec)" role="img" aria-label="Model in a black kaftan dress"></div>
<div class="card-img" style="left:978px;top:2437px;background:linear-gradient(180deg,#f3f3f3,#e7e3de 50%,#f6f6f5)" role="img" aria-label="Model in a white asymmetric dress"></div>

<div class="card-name" style="left:29px;top:2360px">Textured vegan leather</div><div class="card-price" style="left:29px;top:2386px">$ 69.00</div>
<div class="card-name" style="left:272px;top:2360px">Textured vegan leather</div><div class="card-price" style="left:272px;top:2386px">$ 69.00</div>
<div class="card-name" style="left:510px;top:2360px">Textured vegan leather</div><div class="card-price" style="left:510px;top:2386px">$ 69.00</div>
<div class="card-name" style="left:750px;top:2360px">Textured vegan leather</div><div class="card-price" style="left:750px;top:2386px">$ 69.00</div>
<div class="card-name" style="left:980px;top:2360px">Textured vegan leather</div><div class="card-price" style="left:980px;top:2386px">$ 69.00</div>
<div class="card-name" style="left:29px;top:2713px">Textured vegan leather</div><div class="card-price" style="left:29px;top:2739px">$ 69.00</div>
<div class="card-name" style="left:272px;top:2713px">Textured vegan leather</div><div class="card-price" style="left:272px;top:2739px">$ 69.00</div>
<div class="card-name" style="left:510px;top:2713px">Textured vegan leather</div><div class="card-price" style="left:510px;top:2739px">$ 69.00</div>
<div class="card-name" style="left:750px;top:2713px">Textured vegan leather</div><div class="card-price" style="left:750px;top:2739px">$ 69.00</div>
<div class="card-name" style="left:980px;top:2713px">Textured vegan leather</div><div class="card-price" style="left:980px;top:2739px">$ 69.00</div>

<div class="btn btn-sand" style="left:524px;top:2797px;width:216px;height:44px">View All Collection
  <svg width="20" height="10" viewBox="0 0 20 10"><path d="M0 5h18M14 1l4 4-4 4" fill="none" stroke="#24232f" stroke-width="1.6"/></svg></div>

<!-- feed -->
<div class="abs" style="left:0;top:2880px;width:1200px;height:93px;background:linear-gradient(180deg,#fff,#f7f5f7)"></div>
<div class="abs" style="left:441px;top:2914px;display:flex;align-items:center;gap:14px;font-size:23px;font-weight:600;color:#a4387a">
  <span style="width:16px;height:16px;border-radius:50%;background:#a4387a"></span>Follow Our Snapshare</div>
<div class="gram-tile" style="left:0;background:linear-gradient(180deg,#c8ced6,#8d97a4 60%,#d9d5cf)" role="img" aria-label="Woman in a floral dress on a beach"></div>
<div class="abs" style="left:16px;top:2980px;font-size:10px;letter-spacing:1px;color:#4d4d55">#snapgood</div>
<div class="gram-tile" style="left:201px;background:linear-gradient(180deg,#b75d45,#e5b930 55%,#7a8ea0)" role="img" aria-label="Woman in a yellow dress leaping against a brick wall"></div>
<div class="gram-tile" style="left:402px;background:linear-gradient(180deg,#ececec,#c9c4c2 50%,#2a2628)" role="img" aria-label="Woman in a white crop top and black trousers on draped fabric"></div>
<div class="gram-tile" style="left:603px;background:linear-gradient(180deg,#6a6a3e,#b37a52 50%,#c56a3c)" role="img" aria-label="Woman in a patterned shirt outdoors"></div>
<div class="gram-tile" style="left:804px;background:linear-gradient(180deg,#e6eaee,#bc8a82 55%,#a9b4bc)" role="img" aria-label="Woman in a pink tulle dress standing in water"></div>
<div class="gram-tile" style="left:1005px;width:195px;background:linear-gradient(180deg,#c3c8cc,#5c5456 45%,#e3b9b4)" role="img" aria-label="Woman in a black top and pink pleated skirt on a street"></div>

<!-- footer -->
<footer class="footer">
  <div class="logo" style="left:162px;top:90px;color:#fff">SERAH</div>
  <h5 style="left:325px;top:62px">About us</h5>
  <a style="left:325px;top:104px">Store Locator</a>
  <a style="left:325px;top:132px">Lumen Group</a>
  <a style="left:325px;top:160px">Sustainability</a>
  <a style="left:325px;top:188px">Fondazione Lumen</a>
  <a style="left:325px;top:216px">Work with us</a>
  <h5 style="left:498px;top:62px">Legal</h5>
  <a style="left:498px;top:104px">Terms and Conditions of Use</a>
  <a style="left:498px;top:132px">Privacy Policy</a>
  <a style="left:498px;top:160px">Cookie Policy</a>
  <h5 style="left:741px;top:62px">Sign up for newsletter</h5>
  <div class="note" style="left:741px;top:96px">Subscribe to the newsletter to receive updates about<br>collections, events, campaigns and special projects</div>
  <div class="news-input">Your email address<b>SUBSCRIBE</b></div>
  <div class="note" style="left:742px;top:213px">Follow us</div>
  <span class="social" style="left:802px;top:217px"></span>
  <span class="social" style="left:836px;top:217px"></span>
  <span class="social" style="left:872px;top:217px"></span>
  <div class="note" style="left:0;top:286px;width:1200px;text-align:center;font-size:10px;color:#8e8ba8">© SERAH 2020 - 2021 . All Rights Reserved</div>
</footer>

</body>
</html>
```